High impact classy folder for an HVAC and Electrical contractor

We need a folder designed. It needs to be high impact and classy with a rich look to it. We want to cement our branding via the use of the folder so the look will need to have impact with use of our logo and colors.

We want to pull the entire brand look and feel together with this folder. We are going to be making other marketing materials and this is the start of a much larger project. In the ideal situation the winning desginer will continue on with the rest of the projects because they will know how to apply the brand look.

We want to give our local company the feel of a national franchise. Wherein the brand is very prominent and is repeated over and over again.

Use of logo and color scheme will be important.

We like dark backgrounds because they really make the logo pop.

Target Market(s)

homeowners

Font styles to use
Serif

Requirements
Must have
• Logo prominent on the front
• Our Tag Line:
• The Best Way To Live In New Jersey Is With Harbel"
• On the inside pockets:
• Our Phone number: 973-555-0148
• A message to our customers:
• We want to thank you for choosing Harbel Tradeworks today
• Our name says it all, because for over 30 years we have prided ourselves on delivering the best service and exceeding our customers' expectations everyday. Whether you need something fixed, replaced or upgraded, no matter how large or small, the dedicated and experts at Harbel Tradeworks are here to take care of you. Delivering the right solution for you the first time- everytime - and ensuring you are always 100% satisfied. If for any reason you want to speak with us, please do not hesitate to call or email. Thank you again for choosing Harbel Tradeworks.
• On the rear: a graphic that says 24-7 service
• A list of other services we provide:
• Solar
• Generators
• Home Security
• Home Automation
• Home Inspection
• Energy Audits
• 1 Day Bathroom remodles
• Basement Waterproofing
• Garage Doors
• Home Theaters
Nice to have
• I added photos of a flyer and of a mobile website to give an idea of the color scheme as well

```html
<!DOCTYPE html>
<html lang="en">
<head>
<meta charset="utf-8">
<title>Harbel Tradeworks – Presentation Folder</title>
<link rel="stylesheet" href="https://fonts.googleapis.com/css2?family=Cinzel:wght@600;700&family=Open+Sans:ital,wdth,wght@0,75..100,400;0,75..100,700&family=Playfair+Display:wght@700&display=swap">
<style>
  :root {
    --backdrop: #d9bfa2;
    --red-deep: #861219;
    --red: #a8231f;
    --orange: #d4672e;
    --orange-bright: #ef8a3c;
    --gold: #e8c98c;
    --silver: #c9c9cc;
    --silver-dark: #8f9094;
    --paper: #ffffff;
    --paper-grey: #dcdcdc;
    --mark-grey: #8a8a8a;
    --card: #2b2b2b;
  }
  * { box-sizing: border-box; margin: 0; padding: 0; }
  html, body { width: 1200px; height: 847px; overflow: hidden; }
  body {
    background: var(--backdrop);
    position: relative;
    font-family: "Open Sans", sans-serif;
  }

  .panel {
    position: absolute;
    width: 330px;
    height: 440px;
    overflow: hidden;
  }

  /* Front cover */
  .front-cover {
    left: 80px; top: 203px;
    background: linear-gradient(160deg, var(--red-deep) 0%, var(--red) 35%, var(--orange) 60%, var(--red) 100%);
  }
  .front-cover .swoosh { position: absolute; left: 0; top: 0; width: 330px; height: 110px; }
  .front-cover .brand-name {
    position: absolute; left: 0; right: 0; top: 160px;
    text-align: center;
    font-family: "Playfair Display", serif;
    font-weight: 700;
    font-size: 44px;
    line-height: 1.05;
    color: var(--gold);
  }
  .front-cover .tagline-band {
    position: absolute; left: 0; right: 0; top: 362px; height: 26px;
    background: linear-gradient(180deg, #eeeeee, var(--silver) 60%, var(--silver-dark));
    display: flex; align-items: center; justify-content: center;
  }
  .front-cover .tagline {
    font-family: "Cinzel", serif; font-weight: 600;
    font-size: 10.5px; color: var(--red-deep); white-space: nowrap;
  }
  .front-cover .rule {
    position: absolute; left: 0; right: 0; top: 402px; height: 2px; background: var(--silver);
  }
  .front-cover .web-address {
    position: absolute; left: 50%; top: 396px; transform: translateX(-50%);
    background: var(--orange); color: #fff; border-radius: 7px;
    font-size: 7px; padding: 2px 10px; white-space: nowrap;
  }

  /* Inside spread */
  .inside-left { left: 460px; top: 203px; background: var(--paper); }
  .inside-right { left: 790px; top: 203px; background: var(--paper-grey); }
  .inside-mark {
    position: absolute; left: 0; right: 0; top: 70px;
    text-align: center;
    font-family: "Playfair Display", serif; font-weight: 700;
    font-size: 40px; line-height: 1.05; color: var(--mark-grey);
  }
  .pocket {
    position: absolute; left: 0; right: 0; bottom: 0; height: 160px;
    background: linear-gradient(165deg, var(--orange-bright) 0%, var(--orange) 40%, var(--red) 100%);
  }
  .pocket.message { padding: 14px 16px 0 40px; color: #fff; }
  .message-title { font-weight: 700; font-size: 7.5px; margin-bottom: 4px; }
  .message-body { font-size: 5.4px; line-height: 1.75; font-stretch: 80%; }
  .call-line {
    margin-top: 8px;
    font-weight: 700; font-stretch: 75%; font-size: 24px; white-space: nowrap;
  }
  .call-line .phone { color: #ffc58a; }

  .business-card {
    position: absolute; left: 90px; top: 32px; width: 140px; height: 86px;
    background: var(--card);
    border-top: 4px solid var(--orange-bright);
    border-bottom: 4px solid var(--orange-bright);
  }
</style>
</head>
<body>

<section class="panel front-cover" aria-label="Front cover">
  <svg class="swoosh" viewBox="0 0 330 110" aria-hidden="true">
    <path d="M0 0 H330 V62 Q200 10 0 90 Z" fill="#e58a2e"/>
    <path d="M0 90 Q200 10 330 62 V78 Q200 30 0 96 Z" fill="#c7cbd4"/>
    <path d="M0 96 Q200 30 330 78 V84 Q200 40 0 100 Z" fill="#9aa3bf"/>
    <path d="M0 0 H330 V52 Q200 0 0 78 Z" fill="var(--red-deep)"/>
  </svg>
  <h1 class="brand-name">Harbel<br>Tradeworks</h1>
  <div class="tagline-band"><p class="tagline">The Best Way To Live In New Jersey Is With Harbel"</p></div>
  <div class="rule"></div>
  <p class="web-address">www.harbeltradeworks.com</p>
</section>

<section class="panel inside-left" aria-label="Inside left pocket">
  <p class="inside-mark">Harbel<br>Tradeworks</p>
  <div class="pocket message">
    <p class="message-title">We want to thank you for choosing Harbel Tradeworks today</p>
    <p class="message-body">Our name says it all, because for over 30 years we have prided ourselves on delivering the best service and exceeding our customers' expectations everyday. Whether you need something fixed, replaced or upgraded, no matter how large or small, the dedicated and experts at Harbel Tradeworks are here to take care of you. Delivering the right solution for you the first time- everytime - and ensuring you are always 100% satisfied. If for any reason you want to speak with us, please do not hesitate to call or email. Thank you again for choosing Harbel Tradeworks.</p>
    <p class="call-line">Call Us <span class="phone">973-555-0148</span></p>
  </div>
</section>

<section class="panel inside-right" aria-label="Inside right pocket">
  <p class="inside-mark">Harbel<br>Tradeworks</p>
  <div class="pocket">
    <div class="business-card" aria-label="Business card slot"></div>
  </div>
</section>

</body>
</html>
```